Business Card Design For A Cajun Seafood Restaurant

We are opening a cajun seafood restaurant in a week. We mainly serve cajun seafood which is orginally from Louisiana. We want design on both sides of a business card. I have menu on the website. You can go to www.reednkettle.example to check out our menu.

Restaurant name: Reed N' Kettle
Phone: +1 (555) 304-7712
Address: 48206 Ludlow Row, #7, Bexmoor Flats, Ca90000
Email: reednkettle@mailbox.example
Website: www.reednkettle.example

Maybe add social media icons (facebook, instagram) if looks nice on the business card.
facebook.com/reednkettle
instagram.com/reednkettle or @reednkettle

Attached is the logo and other business card samples that I like.

```html
<!DOCTYPE html>
<html lang="en">
<head>
<meta charset="utf-8">
<title>Reed N' Kettle – Business Cards</title>
<link href="https://fonts.googleapis.com/css2?family=Roboto:wght@400;500&display=swap" rel="stylesheet">
<style>
  :root {
    --page: #e6e6e6;
    --kraft: #c9a678;
    --kraft-dark: #b8925f;
    --ink: #1e1a16;
    --ink-soft: #2b2520;
    --paper: #ececec;
    --crab: #d0612a;
    --corn: #e0b032;
    --band-yellow: #dcaf22;
    --band-orange: #d2612a;
    --white: #ffffff;
  }
  * { box-sizing: border-box; margin: 0; padding: 0; }
  html, body { width: 1200px; height: 576px; overflow: hidden; }
  body {
    background: var(--page);
    font-family: "Roboto", Arial, sans-serif;
    color: var(--ink);
    position: relative;
  }
  .card {
    position: absolute;
    top: 139px;
    width: 484px;
    height: 293px;
    border-radius: 5px;
    overflow: hidden;
    background: radial-gradient(ellipse at 40% 35%, var(--kraft) 0%, var(--kraft) 55%, var(--kraft-dark) 100%);
  }
  .card--front { left: 82px; }
  .card--back { left: 602px; width: 481px; }

  .mascot {
    position: absolute;
    border-radius: 40%;
    background: radial-gradient(circle at 50% 55%, var(--crab) 0%, var(--crab) 45%, rgba(224,176,50,0.85) 70%, rgba(201,166,120,0) 100%);
  }
  .card--front .mascot { left: 194px; top: 43px; width: 112px; height: 102px; }
  .card--back .mascot { left: 24px; top: 19px; width: 134px; height: 130px; }

  .brand-name {
    position: absolute;
    font-weight: 500;
    color: var(--ink);
    white-space: nowrap;
    letter-spacing: 0.5px;
  }
  .card--front .brand-name { left: 0; right: 0; top: 150px; text-align: center; font-size: 32px; }
  .card--back .brand-name { right: 24px; top: 36px; font-size: 28px; }

  .torn-edge { position: absolute; left: 0; bottom: 0; width: 100%; height: 52px; }
  .front-web {
    position: absolute; left: 0; right: 0; top: 262px;
    text-align: center; font-size: 14px; color: var(--ink-soft);
  }

  .person { position: absolute; right: 24px; top: 137px; text-align: right; }
  .person__name { font-size: 19px; font-weight: 500; line-height: 1.2; }
  .person__title { font-size: 11px; margin-top: 3px; }
  .divider { position: absolute; left: 26px; top: 174px; width: 324px; height: 1px; background: var(--ink-soft); }

  .contacts { position: absolute; left: 30px; top: 192px; list-style: none; }
  .contacts li { display: flex; align-items: center; height: 18px; font-size: 12.5px; color: var(--ink-soft); }
  .contacts svg { width: 11px; height: 11px; margin-right: 8px; fill: var(--ink-soft); }

  .address {
    position: absolute; right: 24px; top: 205px;
    text-align: right; font-size: 13px; line-height: 18px; font-style: normal; color: var(--ink-soft);
  }
  .bands { position: absolute; left: 0; bottom: 0; width: 100%; height: 39px; }
  .back-web {
    position: absolute; right: 24px; top: 263px;
    font-size: 12.5px; color: var(--white);
  }
</style>
</head>
<body>

  <section class="card card--front" aria-label="Business card front">
    <div class="mascot" role="img" aria-label="Illustrated restaurant mascot holding an ear of corn"></div>
    <div class="brand-name">Reed N' Kettle</div>
    <svg class="torn-edge" viewBox="0 0 484 52" preserveAspectRatio="none" aria-hidden="true">
      <path fill="var(--paper)" d="M0 8 L20 6 L38 9 L60 5 L84 8 L110 4 L132 7 L158 5 L182 9 L206 6 L230 8 L256 4 L280 7 L306 5 L330 8 L354 4 L380 7 L404 5 L428 8 L452 4 L470 7 L484 5 L484 52 L0 52 Z"/>
    </svg>
    <div class="front-web">www.reednkettle.example</div>
  </section>

  <section class="card card--back" aria-label="Business card back">
    <div class="mascot" role="img" aria-label="Illustrated restaurant mascot holding an ear of corn"></div>
    <div class="brand-name">Reed N' Kettle</div>

    <div class="person">
      <div class="person__name">Dana Whitlow</div>
      <div class="person__title">Managing Director</div>
    </div>
    <div class="divider"></div>

    <ul class="contacts">
      <li><svg viewBox="0 0 12 12" aria-hidden="true"><path d="M1 3 Q1 1 3 1 L9 1 Q11 1 11 3 L11 4 L8 4 L8 3 L4 3 L4 4 L1 4 Z M3 5 L9 5 L10.5 10.5 L1.5 10.5 Z"/></svg>+1 (555) 304-7712</li>
      <li><svg viewBox="0 0 12 12" aria-hidden="true"><path d="M0.5 2.5 H11.5 V9.5 H0.5 Z" fill="none" stroke="currentColor"/><path d="M0.5 2.5 L6 7 L11.5 2.5 V2 H0.5 Z"/></svg>reednkettle@mailbox.example</li>
      <li><svg viewBox="0 0 12 12" aria-hidden="true"><rect x="0.5" y="0.5" width="11" height="11" rx="1.5"/></svg>facebook.com/reednkettle</li>
      <li><svg viewBox="0 0 12 12" aria-hidden="true"><rect x="0.5" y="0.5" width="11" height="11" rx="1.5"/></svg>instagram.com/reednkettle</li>
    </ul>

    <address class="address">48206 Ludlow Row, #7,<br>Bexmoor Flats, Ca90000</address>

    <svg class="bands" viewBox="0 0 481 39" preserveAspectRatio="none" aria-hidden="true">
      <rect x="0" y="18" width="270" height="21" fill="var(--band-yellow)"/>
      <path d="M270 0 L481 0 L481 39 L254 39 Z" fill="var(--band-orange)"/>
    </svg>
    <div class="back-web">www.reednkettle.example</div>
  </section>

</body>
</html>
```